Business Card Design Project

I need a business card designed from scratch. I have an existing logo that I can upload in Illustrator for modification or redesign.

The Company is called Query Lanterns http://querylanterns.com.au and we provide Search Engine Optimization services to Australian businesses. The current logo signifies an increase in visitors, profits etc...

There are no restrictions as to the redesign - colours, style etc are all open to change.

Cards will be full colour and one sided printed at http://www.cardmoxel.com.au so check their requirements for file format and sizes etc.

I will expect all original files upon completion of project.

Target Market(s)

Any business with a web site looking to improve their search engine rankings

Industry/Entity Type

Business

Requirements
Must have
• I like modern, sleek designs. Clean, not fussy, uncluttered.

```html
<!DOCTYPE html>
<html lang="en">
<head>
<meta charset="utf-8">
<title>Query Lanterns – Business Card</title>
<link rel="stylesheet" href="https://fonts.googleapis.com/css2?family=Open+Sans:wght@400;600;800&display=swap">
<style>
  :root {
    --brand-blue: #2f6db3;
    --brand-blue-deep: #1f5a9e;
    --brand-yellow: #f2c12e;
    --brand-amber: #e3a51f;
    --ink: #1b1b1b;
    --ink-soft: #555;
    --paper: #ffffff;
    --backdrop: #e9e7e3;
  }
  * { box-sizing: border-box; margin: 0; padding: 0; }
  html, body {
    width: 1200px; height: 900px; overflow: hidden;
    background: var(--backdrop);
    font-family: "Open Sans", Arial, sans-serif;
  }
  .canvas {
    width: 1200px; height: 900px;
    display: flex; align-items: center; justify-content: center;
  }
  .card {
    position: relative;
    width: 470px; height: 770px;
    background: var(--paper);
    overflow: hidden;
    box-shadow: 0 12px 30px rgba(0,0,0,.18);
  }
  .logo {
    position: absolute; top: 78px; left: 150px;
    display: flex; align-items: center; gap: 12px;
  }
  .logo-dot {
    width: 20px; height: 20px; border-radius: 50%;
    background: var(--brand-yellow);
  }
  .logo-name {
    font-weight: 800; font-size: 38px; line-height: 1;
    color: var(--brand-blue); letter-spacing: -0.5px;
  }
  .accent-bar {
    position: absolute; left: 0; top: 176px;
    width: 30px; height: 150px;
  }
  .accent-bar .top { height: 55%; background: var(--brand-blue); }
  .accent-bar .bottom { height: 45%; background: var(--brand-yellow); }
  .contact {
    position: absolute; top: 190px; left: 58px;
  }
  .contact-name {
    font-size: 26px; font-weight: 600; color: var(--ink);
    letter-spacing: 0.5px;
  }
  .contact-role {
    font-size: 13px; color: var(--ink-soft); margin-bottom: 18px;
  }
  .contact-list { list-style: none; }
  .contact-list li {
    display: flex; align-items: center; gap: 12px;
    font-size: 16px; color: var(--ink); margin-bottom: 8px;
  }
  .contact-list svg { width: 16px; height: 16px; flex: none; }
  .ribbon-art {
    position: absolute; left: 0; bottom: 0;
    width: 100%; height: 400px;
    background: linear-gradient(160deg, var(--brand-yellow) 0%, var(--brand-amber) 55%, var(--brand-blue) 100%);
    clip-path: polygon(0 8%, 100% 0, 100% 100%, 0 100%);
  }
</style>
</head>
<body>
<main class="canvas">
  <article class="card">
    <div class="logo">
      <span class="logo-dot"></span>
      <span class="logo-name">Query Lanterns</span>
    </div>

    <div class="accent-bar"><div class="top"></div><div class="bottom"></div></div>

    <section class="contact">
      <h1 class="contact-name">SAM KELLER</h1>
      <p class="contact-role">Owner</p>
      <ul class="contact-list">
        <li>
          <svg viewBox="0 0 16 16"><path d="M4 1 L6 5 L4.5 6.5 C5.5 8.5 7.5 10.5 9.5 11.5 L11 10 L15 12 L13.5 15 C7 14.5 1.5 9 1 2.5 Z" fill="var(--brand-blue)"/></svg>
          1300 555 018
        </li>
        <li>
          <svg viewBox="0 0 16 16"><rect x="1" y="3" width="14" height="10" fill="none" stroke="var(--brand-blue)" stroke-width="1.5"/><path d="M1 3 L8 9 L15 3" fill="none" stroke="var(--brand-blue)" stroke-width="1.5"/></svg>
          enquiry@querylanterns.com.au
        </li>
        <li>
          <svg viewBox="0 0 16 16"><circle cx="8" cy="8" r="6.5" fill="none" stroke="var(--brand-blue)" stroke-width="1.3"/><ellipse cx="8" cy="8" rx="3" ry="6.5" fill="none" stroke="var(--brand-blue)" stroke-width="1.1"/><path d="M1.5 8 H14.5" stroke="var(--brand-blue)" stroke-width="1.1"/></svg>
          www.querylanterns.com.au
        </li>
      </ul>
    </section>

    <div class="ribbon-art" role="img" aria-label="Large yellow and blue zigzag ribbon rising into an arrow, the brand growth motif"></div>
  </article>
</main>
</body>
</html>
```